creation of a business card design for a company specializing in the creation...

I would like to create a design for a professional business card on a black background and with the company's colors (I am attaching some files: including the logo in horizontal and centered format, I am also attaching a recent project design a T-shirt, this is the one I chose to give you an idea of my preferences.

we are in the process of developing a new website design, it is still in the development phase but it can be viewed at the following address: www.vantrelmo.be to give you other ideas about the company
you will see for yourself the subject of my main activity: company specializing in the construction of stairs

I would like a business card that stands out from the rest with a unique design

here is the informations
Name: Lucien Barthel
Function: Manager
Address: Rue Moulinet du Parc 42
7180 La Louvière
telephone: +32 468 219 804
email: info@rx7p.be
website: rx7p. be
social networks: Facebook, YouTube, TikTok, Instagram

Target Market(s)

customer who wants to have a beautiful staircase built

Industry/Entity Type

contruction d'escalier

Contact Information for Business Card

Adresse. Numero de telephone, site web, le texte : "Createur d'escalier", logo recto-verso, icone des reseaux sociaux

Requirements
Must have
• the mention: Stair creator
Nice to have
• an illustration of a designer staircase
Should not have
• do not distort the logo

```html
<!DOCTYPE html>
<html lang="fr">
<head>
<meta charset="utf-8">
<title>RX7P – carte de visite</title>
<link rel="stylesheet" href="https://fonts.googleapis.com/css2?family=Open+Sans:wght@400;600;700&display=swap">
<style>
  :root {
    --stage: #232323;
    --card: #1d1e21;
    --card-deep: #0e0f11;
    --edge: #5b8db5;
    --accent: #6a9ac2;
    --accent-soft: #9bb9d3;
    --ink: #f2f2f2;
    --silver: #a9a9ab;
    --graphite: #3a3b3e;
  }
  * { box-sizing: border-box; margin: 0; padding: 0; }
  html, body { width: 1200px; height: 780px; overflow: hidden; }
  body {
    background: var(--stage);
    font-family: "Open Sans", Arial, sans-serif;
    color: var(--ink);
  }
  .canvas {
    position: relative;
    width: 1200px; height: 780px;
    display: flex; align-items: center; justify-content: center; gap: 40px;
  }
  .card {
    position: relative;
    width: 540px; height: 309px;
    background: var(--card);
    border-bottom: 5px solid var(--edge);
    overflow: hidden;
    box-shadow: 0 18px 40px rgba(0,0,0,.55);
  }

  /* back side */
  .card-back__pattern {
    position: absolute; inset: 0;
    background: linear-gradient(200deg, var(--silver) 0%, var(--graphite) 24%, var(--card) 45%, var(--card-deep) 100%);
  }
  .card-back__brand {
    position: absolute; right: 34px; bottom: 30px;
    display: flex; align-items: center; gap: 10px;
  }
  .brand-square { width: 18px; height: 18px; background: var(--accent); }
  .brand-name {
    font-weight: 600; font-size: 26px; letter-spacing: 3px; color: var(--ink);
  }

  /* front side */
  .card-front__tagline {
    position: absolute; left: 36px; top: 14px;
    font-weight: 600; font-size: 12px; letter-spacing: 1.5px;
    text-transform: uppercase; color: var(--ink);
  }
  .card-front__emblem {
    position: absolute; left: 46px; top: 36px;
    width: 118px; height: 118px; border-radius: 50%;
    background: radial-gradient(circle at 50% 45%, #2f5f7c 0%, #1f3f55 45%, #3b3d42 75%, var(--card) 100%);
  }
  .card-front__brand {
    position: absolute; left: 70px; top: 156px;
    font-weight: 600; font-size: 15px; letter-spacing: 3px; color: var(--ink);
  }
  .card-front__details {
    position: absolute; left: 40px; right: 30px; bottom: 24px;
  }
  .person {
    display: flex; align-items: baseline; gap: 10px; margin-bottom: 6px;
  }
  .person__name { font-weight: 700; font-size: 30px; line-height: 1.1; }
  .person__first { color: var(--accent-soft); }
  .person__last { color: var(--accent); }
  .person__role { font-size: 15px; font-weight: 400; color: var(--ink); }
  .person__web { margin-left: auto; }
  .contact-row {
    display: flex; gap: 34px; font-size: 15px; line-height: 1.6;
  }
  .label { color: var(--accent); font-weight: 600; margin-right: 6px; }
</style>
</head>
<body>
<main class="canvas">

  <section class="card card-back">
    <div class="card-back__pattern" role="img" aria-label="Repeating pattern of the brand symbol in diagonal rows, glossy silver at the top right fading into black"></div>
    <div class="card-back__brand">
      <span class="brand-square"></span>
      <span class="brand-name">RX7P</span>
    </div>
  </section>

  <section class="card card-front">
    <p class="card-front__tagline">Créateur d'escalier</p>
    <div class="card-front__emblem" role="img" aria-label="Round emblem with an illustrated floating staircase"></div>
    <p class="card-front__brand">RX7P</p>
    <div class="card-front__details">
      <div class="person">
        <span class="person__name"><span class="person__first">Lucien</span> <span class="person__last">Barthel</span></span>
        <span class="person__role">Manager</span>
        <span class="person__web contact-row"><span><span class="label">W:</span>www.rx7p.be</span></span>
      </div>
      <div class="contact-row">
        <span><span class="label">T:</span>+32 468 219 804</span>
        <span><span class="label">E:</span>info@rx7p.be</span>
      </div>
      <div class="contact-row">
        <span><span class="label">L:</span>Rue Moulinet du Parc 42 7180 La Louvière</span>
      </div>
    </div>
  </section>

</main>
</body>
</html>
```